Business Card Design

We like to use greens as you will see in our logo (but not TOO much green). We are a Dental Clinic in a somewhat eccentric community. We do not like the dated sharp designs which we see many dentists use. We're looking for something bright and fresh while still maintaining the integrity of the profession. Elegance is not necessarily what we are going for... we need for the design to be "mature" but also up-lifting.

See our logo.
Updates

Project Deadline Extended
Reason: We have 5 designs which we like. But we'd like to see a few more before committing to a design.

Project Deadline Extended
Reason: We are awaiting revisions to this project. We are still welcoming designs while we wait to see if designers are able to provide to us the revisions we require in order to proceed with a selection.

Target Market(s)

Younger families - ages late 20's to early 40's

Industry/Entity Type

Business

Contact Information for Business Card

Corwel T. Banfry DDS 2730 W. Halvert Rd. Ste. 7 Larkmoor, NV 48391 (248)555-0174 FX (248)555-0189 info@BrightwellDentalCareMi.com BrigthwellDentalCareMi.com on the back of the card we need an appointment reminder (For____ Date___ Time____) with "If you are unable to keep your appointment, kindly give 48 hours notice" at the bottom. No use of teeth in the design. DOUBLE SIDED DESIGN

Requirements
Should not have
• The use of pictures of teeth

```html
<!DOCTYPE html>
<html lang="en">
<head>
<meta charset="utf-8">
<title>Brightwell Dental Care – Business Card</title>
<link href="https://fonts.googleapis.com/css2?family=Source+Sans+3:wght@400;600;700&family=Tinos:ital,wght@0,700;1,400&display=swap" rel="stylesheet">
<style>
  :root {
    --bg: #e9e6e1;
    --paper: #ffffff;
    --green-bright: #4ae032;
    --green-dark: #2f7a17;
    --ink: #3d3d3d;
    --box-line: #555555;
  }
  * { box-sizing: border-box; margin: 0; padding: 0; }
  html, body { width: 1200px; height: 492px; overflow: hidden; }
  body {
    background: var(--bg);
    font-family: "Source Sans 3", Arial, sans-serif;
    position: relative;
  }
  .card {
    position: absolute;
    background: var(--paper);
    box-shadow: 0 6px 18px rgba(0,0,0,.25);
    overflow: hidden;
  }

  /* ---------- Front ---------- */
  .card-front { left: 30px; top: 86px; width: 540px; height: 320px; }
  .front-shape { position: absolute; inset: 0; }
  .brand { position: absolute; color: var(--green-dark); font-weight: 600; line-height: 1; }
  .card-front .brand { left: 42px; top: 130px; }
  .brand-name { display: block; font-size: 46px; letter-spacing: -0.5px; }
  .brand-sub { display: block; font-size: 25px; letter-spacing: 0.5px; margin-top: 4px; }
  .contact { position: absolute; right: 24px; top: 26px; width: 220px; color: #fff; text-align: right; }
  .contact-name { font-size: 17px; font-weight: 700; margin-bottom: 18px; white-space: nowrap; }
  .contact-name small { font-size: 13px; font-weight: 700; }
  .contact-address { font-size: 13px; line-height: 1.45; margin-bottom: 26px; }
  .contact-line { font-size: 13px; line-height: 1.6; display: flex; justify-content: flex-end; align-items: center; gap: 5px; white-space: nowrap; }
  .contact-line svg { width: 11px; height: 11px; flex: none; }

  /* ---------- Back ---------- */
  .card-back { left: 606px; top: 86px; width: 564px; height: 320px; }
  .card-back .brand { left: 30px; top: 26px; }
  .card-back .brand-name { font-size: 32px; }
  .card-back .brand-sub { font-size: 17px; margin-top: 2px; }
  .brand-rule { position: absolute; left: 30px; top: 88px; width: 340px; border-top: 1px dotted #999; }
  .appt-title {
    position: absolute; left: 30px; top: 96px;
    font-family: "Tinos", "Times New Roman", serif; font-weight: 700;
    font-size: 16px; color: var(--green-dark); letter-spacing: 0.5px;
  }
  .field { position: absolute; font-size: 15px; line-height: 18px; color: var(--ink); display: flex; align-items: flex-end; gap: 6px; }
  .fill-line { border-bottom: 1px dotted var(--box-line); height: 14px; }
  .slot { position: absolute; border: 1px solid var(--box-line); border-radius: 2px; background: #fff; }
  .days { position: absolute; left: 30px; top: 246px; display: flex; align-items: center; gap: 6px; font-weight: 700; font-size: 14px; color: var(--ink); }
  .day-box { width: 32px; height: 20px; border: 1px solid var(--box-line); border-radius: 2px; margin-right: 6px; }
  .notice {
    position: absolute; left: 30px; right: 20px; top: 282px;
    font-family: "Tinos", "Times New Roman", serif; font-style: italic;
    font-size: 14.5px; color: var(--ink);
  }
</style>
</head>
<body>

<section class="card card-front" aria-label="Business card front">
  <svg class="front-shape" viewBox="0 0 540 320" preserveAspectRatio="none" aria-hidden="true">
    <path d="M262 0 C330 70 325 230 215 320 L540 320 L540 0 Z" fill="var(--green-dark)"/>
    <path d="M290 0 C350 75 340 235 236 320 L540 320 L540 0 Z" fill="var(--green-bright)"/>
  </svg>

  <div class="brand">
    <span class="brand-name">Brightwell</span>
    <span class="brand-sub">DENTAL CARE</span>
  </div>

  <div class="contact">
    <p class="contact-name">Corwel T. Banfry, <small>DDS</small></p>
    <p class="contact-address">2730 W. Halvert Rd. Ste.<br>7 Larkmoor, NV 48391</p>
    <p class="contact-line">
      <svg viewBox="0 0 12 12"><circle cx="6" cy="6" r="5.5" fill="none" stroke="#fff"/><path d="M4 3.5l1 1-0.7 1c.4.8 1 1.4 1.8 1.8l1-.7 1 1-.8 1C5.6 8.5 3.5 6.4 3.4 4.3z" fill="#fff"/></svg>
      (555)555-0174
    </p>
    <p class="contact-line">
      <svg viewBox="0 0 12 12"><rect x="1" y="4" width="10" height="6" rx="1" fill="#fff"/><rect x="3" y="1.5" width="6" height="3" fill="none" stroke="#fff"/></svg>
      FX (555)555-0189
    </p>
    <p class="contact-line">
      <svg viewBox="0 0 12 12"><rect x="1" y="2.5" width="10" height="7" rx="1" fill="#fff"/><path d="M1.5 3l4.5 3.5L10.5 3" fill="none" stroke="var(--green-bright)"/></svg>
      info@BrightwellDentalCareMi.com
    </p>
    <p class="contact-line">
      <svg viewBox="0 0 12 12"><circle cx="6" cy="6" r="5" fill="none" stroke="#fff"/><ellipse cx="6" cy="6" rx="2" ry="5" fill="none" stroke="#fff"/><path d="M1 6h10" stroke="#fff"/></svg>
      www.BrigthwellDentalCareMi.com
    </p>
  </div>
</section>

<section class="card card-back" aria-label="Appointment reminder card back">
  <div class="brand">
    <span class="brand-name">Brightwell</span>
    <span class="brand-sub">DENTAL CARE</span>
  </div>
  <div class="brand-rule"></div>
  <h2 class="appt-title">YOUR APPOINTMENT</h2>

  <div class="field" style="left:30px; top:124px;">Name :<span class="fill-line" style="width:300px"></span></div>
  <div class="field" style="left:190px; top:150px;">Time :<span class="fill-line" style="width:130px"></span>am / pm</div>
  <div class="field" style="left:30px; top:180px;">Date :<span class="fill-line" style="width:100px"></span></div>
  <div class="slot" style="left:180px; top:176px; width:92px; height:22px;"></div>
  <div class="slot" style="left:298px; top:170px; width:92px; height:22px;"></div>
  <div class="field" style="left:30px; top:214px;">Next Appointment</div>
  <div class="slot" style="left:172px; top:210px; width:90px; height:22px;"></div>

  <div class="days">
    <span>MON</span><span class="day-box"></span>
    <span>TUE</span><span class="day-box"></span>
    <span>WED</span><span class="day-box"></span>
    <span>THU</span><span class="day-box"></span>
    <span>FRI</span><span class="day-box"></span>
    <span>SAT</span><span class="day-box"></span>
  </div>

  <p class="notice">If you are unable to keep your appointment, kindly give 48 hours notice</p>
</section>

</body>
</html>
```